Landingpage design

We need a landingpage for a Chatterloom add campaign. We sell socks made of bamboo in super quality. Our customers loves us, and we have a 5 heart rating at scorevane.com.

We want to create a add campaign targeted new customers, and the offer is that they can buy 1 pair of bamboo socks as a test, for only 20 DKK (2,7 Euro) including shipment. Our webpage is www.tuvelo.dk, landingpage should be built i Kyvio, a wysiwyg editor. based on their template. like:
https://tuvelo.pemlorsite.com/13844-sales-page
https://tuvelo.pemlorsite.com/13696-sales-page
https://tuvelo.pemlorsite.com/13845-sales-page

You don't have to follow the templates 100% if you have better ideas. We have an account for snapvaultly, so please get stockphotos from here.

Bamboo socks has a lot of great selling points, you can see a good desciption here:
https://feltrano.com/us/why-bamboo

We expect you to have experience in landingpage design, and expect to end up with 2 landingpages we can splittest on.

This is the first of a number of landingpages we need in the future, so for the right person there will be plenty of more work.

Target Market(s)

Denmark

Industry/Entity Type

E-Commerce

Number of Pages Required

2 page

Colors

Designer to choose colors to be used in the design.

Requirements
Must have
• A great selling page, showing all the great things with bamboo socks. It should be supplied with good packshots from snapvaultly.com

```html
<!DOCTYPE html>
<html lang="en">
<head>
<meta charset="utf-8">
<title>Tuvelo – Bamboo Socks</title>
<link rel="stylesheet" href="https://fonts.googleapis.com/css2?family=Roboto:wght@400;500;700&display=swap">
<style>
:root{
  --cyan:#7cdcf0;
  --blue:#62a3ea;
  --green:#38b486;
  --green-dark:#2e9c73;
  --star:#f8bf1a;
  --ink:#555a60;
  --muted:#7b7f85;
  --grey-bg:#f1f1f1;
  --footer:#1f2231;
  --white:#ffffff;
  --photo-light:#eef3f0;
  --photo-mid:#d6e8de;
}
*{box-sizing:border-box;margin:0;padding:0}
html,body{width:1200px;height:2765px;overflow:hidden}
body{font-family:"Roboto",Arial,sans-serif;color:var(--ink);background:var(--white);position:relative}
.section{position:absolute;left:0;width:1200px}
.abs{position:absolute}
.center{text-align:center;left:0;width:1200px}
.section-title{font-size:35px;font-weight:400;color:var(--ink)}
.section-title .mark{position:relative;display:inline-block}
.section-title .mark::after{content:"";position:absolute;left:0;right:0;bottom:-6px;height:2px;background:currentColor;opacity:.6}
.section-lead{font-size:15.5px;line-height:27px;color:var(--muted)}

/* facts */
.facts{top:0;height:560px;background:linear-gradient(180deg,var(--cyan),var(--blue))}
.facts .section-title,.facts .section-lead{color:var(--white)}
.fact{position:absolute;width:300px;text-align:center;color:var(--white);font-size:15.5px;line-height:27px}
.fact-icon{width:88px;height:88px;border-radius:50%;background:var(--white);margin:0 auto 16px;display:flex;align-items:center;justify-content:center}

/* video */
.video{top:560px;height:727px;background:var(--white)}
.video-frame{left:292px;top:279px;width:615px;height:341px;border-radius:4px;background:linear-gradient(135deg,#eeecef,#e2dde0 50%,#efe9e6)}
.play{left:566px;top:419px;width:66px;height:66px;border-radius:50%;background:var(--green);display:flex;align-items:center;justify-content:center}

/* reviews */
.reviews{top:1287px;height:791px;background:var(--grey-bg)}
.stars{color:var(--star);letter-spacing:2px}
.review-card{position:absolute;top:326px;width:299px;height:271px;background:var(--white);padding:40px 26px 0;text-align:center}
.reviewer{display:flex;align-items:center;justify-content:center;gap:16px;margin-bottom:20px}
.avatar{width:42px;height:42px;border-radius:50%;background:linear-gradient(135deg,#3a78a8,#c98b5e)}
.reviewer-name{font-size:15px;color:var(--ink);text-align:left}
.reviewer .stars{font-size:17px;letter-spacing:0}
.review-text{font-size:14px;line-height:21px;color:var(--muted)}
.arrow{position:absolute;top:448px}
.btn{position:absolute;background:var(--green);color:var(--white);font-size:13px;font-weight:500;text-transform:uppercase;display:flex;align-items:center;justify-content:center;letter-spacing:.3px}

/* offer */
.offer{top:2078px;height:440px;background:var(--white)}
.offer-title{left:134px;top:70px;font-size:44px;font-weight:500;line-height:55px;color:var(--ink)}
.benefits{left:134px;top:195px;list-style:none;font-size:15.5px;color:var(--muted)}
.benefits li{display:flex;align-items:center;gap:10px;height:27.5px}
.offer-note{left:134px;top:344px;font-size:12px;color:var(--muted)}
.model-photo{left:800px;top:42px;width:260px;height:398px;background:linear-gradient(180deg,var(--photo-light),var(--photo-mid))}

/* footer */
.footer{top:2518px;height:247px;background:var(--footer);color:var(--white)}
.footer-col{position:absolute;top:56px;width:300px}
.footer-col h3{font-size:19px;font-weight:500;margin-bottom:12px}
.footer-col p{font-size:12.5px;line-height:18px}
.footer-col a{color:var(--green);text-decoration:none}
.footer-nav{font-size:12.5px}
.social{display:flex;align-items:center;gap:8px;margin-top:10px;font-size:12.5px}
.social .dot{width:20px;height:20px;border-radius:50%;background:var(--white)}
</style>
</head>
<body>

<section class="section facts">
  <h1 class="abs center section-title" style="top:100px">A Few <span class="mark">Facts About</span> Tuvelo</h1>
  <p class="abs center section-lead" style="top:161px">We have been working on textile for more than 10 years. This ensures that all products<br>meet our high quality standards.</p>

  <div class="fact" style="left:133px;top:281px">
    <div class="fact-icon">
      <svg width="34" height="30" viewBox="0 0 34 30"><path d="M11 1 L2 6 L5 13 L9 11 L9 29 L25 29 L25 11 L29 13 L32 6 L23 1 Q17 6 11 1Z" fill="var(--blue)"/></svg>
    </div>
    Our mission is to give our<br>customers access to quality products<br>at a reasonable price.
  </div>
  <div class="fact" style="left:450px;top:281px">
    <div class="fact-icon">
      <svg width="36" height="36" viewBox="0 0 36 36" fill="var(--blue)"><rect x="6" y="4" width="5" height="28" rx="1"/><rect x="15" y="10" width="5" height="22" rx="1"/><path d="M22 6 L32 2 L30 10 Z"/><path d="M11 14 L20 18 L11 22Z"/></svg>
    </div>
    We know that the properties of bamboo<br>are absolutely amazing and can reduce,<br>for example, sweaty and sour toes.
  </div>
  <div class="fact" style="left:767px;top:281px">
    <div class="fact-icon">
      <svg width="32" height="36" viewBox="0 0 32 36"><circle cx="16" cy="13" r="11" fill="none" stroke="var(--blue)" stroke-width="3"/><circle cx="16" cy="13" r="5" fill="var(--blue)"/><path d="M9 22 L6 34 L12 31 L15 35 L16 24 M23 22 L26 34 L20 31 L17 35 L16 24" fill="var(--blue)"/></svg>
    </div>
    We shop directly with the<br>factories. This ensures the highest<br>quality at a competitive price.
  </div>
</section>

<section class="section video">
  <h2 class="abs center section-title" style="top:97px">A Short <span class="mark">Video About</span> Our Work</h2>
  <p class="abs center section-lead" style="top:157px">We sell stockings, t-shirts, sweaters and men's boxershorts. If you choose our<br>subscription service, the products will come to you automatically.</p>
  <svg class="abs" style="left:0;top:432px" width="196" height="60" viewBox="0 0 196 60"><path d="M0 0 H124 V10 H196 L176 32 L196 58 H96 V48 H0Z" fill="var(--green)"/><path d="M96 48 L124 48 L124 38Z" fill="var(--green-dark)"/></svg>
  <svg class="abs" style="left:987px;top:432px" width="213" height="60" viewBox="0 0 213 60"><path d="M213 0 H72 V10 H0 L20 32 L0 58 H100 V48 H213Z" fill="var(--green)"/><path d="M100 48 L72 48 L72 38Z" fill="var(--green-dark)"/></svg>
  <div class="abs video-frame" role="img" aria-label="Flat-lay photo of clothes and shoes laid out beside an open suitcase"></div>
  <div class="abs play"><svg width="26" height="28" viewBox="0 0 26 28"><path d="M4 2 L24 14 L4 26Z" fill="var(--white)"/></svg></div>
</section>

<section class="section reviews">
  <div class="abs center stars" style="top:96px;font-size:34px">★★★★★</div>
  <h2 class="abs center section-title" style="top:143px">We Have <span class="mark">a 5 Stars</span> Rating</h2>
  <p class="abs center section-lead" style="top:207px">You're in a good company. Here are some important facts and<br>testimonials about us.</p>

  <svg class="arrow" style="left:104px" width="14" height="22" viewBox="0 0 14 22"><path d="M11 2 L3 11 L11 20" fill="none" stroke="var(--green)" stroke-width="2.5"/></svg>
  <svg class="arrow" style="left:1082px" width="14" height="22" viewBox="0 0 14 22"><path d="M3 2 L11 11 L3 20" fill="none" stroke="var(--green)" stroke-width="2.5"/></svg>

  <article class="review-card" style="left:134px">
    <div class="reviewer"><div class="avatar" role="img" aria-label="Customer portrait"></div><div><div class="reviewer-name">Rune Falster</div><div class="stars">★★★★★</div></div></div>
    <p class="review-text">Lorem ipsum dolor sit amet, consetetur sadipscing elitr, sed diam nonumy eirmod tempor invidunt ut labore et dolore magna aliquyam erat, sed diam voluptua. At vero eos et accusam et justo duo</p>
  </article>
  <article class="review-card" style="left:450px">
    <div class="reviewer"><div class="avatar" role="img" aria-label="Customer portrait"></div><div><div class="reviewer-name">Rune Falster</div><div class="stars">★★★★★</div></div></div>
    <p class="review-text">Lorem ipsum dolor sit amet, consetetur sadipscing elitr, sed diam nonumy eirmod tempor invidunt ut labore et dolore magna aliquyam erat, sed diam voluptua. At vero eos et accusam et justo duo</p>
  </article>
  <article class="review-card" style="left:767px">
    <div class="reviewer"><div class="avatar" role="img" aria-label="Customer portrait"></div><div><div class="reviewer-name">Rune Falster</div><div class="stars">★★★★★</div></div></div>
    <p class="review-text">Lorem ipsum dolor sit amet, consetetur sadipscing elitr, sed diam nonumy eirmod tempor invidunt ut labore et dolore magna aliquyam erat, sed diam voluptua. At vero eos et accusam et justo duo</p>
  </article>

  <div class="btn" style="left:485px;top:650px;width:229px;height:35px">More Reviews</div>
</section>

<section class="section offer">
  <h2 class="abs offer-title">Get Your First Pair of Bamboo<br>Socks for Only 20 PKK</h2>
  <ul class="abs benefits">
    <li><svg width="16" height="12" viewBox="0 0 16 12"><path d="M1 6 L6 11 L15 1" fill="none" stroke="var(--green)" stroke-width="2"/></svg>Powerfully insulating - keeps you cooler in summer and warmer in winter</li>
    <li><svg width="16" height="12" viewBox="0 0 16 12"><path d="M1 6 L6 11 L15 1" fill="none" stroke="var(--green)" stroke-width="2"/></svg>Antibacterial - keeps you odor free and feeling and smelling fresh</li>
    <li><svg width="16" height="12" viewBox="0 0 16 12"><path d="M1 6 L6 11 L15 1" fill="none" stroke="var(--green)" stroke-width="2"/></svg>Most eco-friendly fabric on the planet - help save your planet</li>
  </ul>
  <div class="btn" style="left:134px;top:297px;width:194px;height:35px">Buy Now</div>
  <p class="abs offer-note">Shipment included</p>
  <div class="abs model-photo" role="img" aria-label="Photo of a model wearing a green bamboo bodysuit"></div>
</section>

<footer class="section footer">
  <div class="footer-col" style="left:134px">
    <h3>About us</h3>
    <p>At Tuvelo.dk we specialize in basic products in bamboo. We sell stockings, t-shirts, sweaters and men's boxershorts</p>
    <div class="social"><span class="dot"></span>Chatterloom</div>
  </div>
  <div class="footer-col" style="left:450px">
    <h3>Contact us</h3>
    <p>Any questions? Then e-mail <a>info@tuvelo.dk</a><br>or call us at +45 61 72 39 04</p>
    <p style="margin-top:6px">Or send us a letter to Tuvelo<br>Kildevej 14<br>7100 Vejle</p>
  </div>
  <div class="footer-col" style="left:767px">
    <h3>Navigation</h3>
    <p class="footer-nav">Home &nbsp;|&nbsp; Why Bamboo &nbsp;|&nbsp; About &nbsp;|&nbsp; Reviews</p>
  </div>
</footer>

</body>
</html>
```